Business card design

I need my logo on this card, things I need the card to have on it
licensed and insured.
owner operators Milo & Trent Halvorsen
my phone number 5083716254
Disaster Recovery, Storm Damage Restoration, Proactive Disaster Plan Management, Roof Repair/Restoration Structural Repair and Reconstruction, Emergency Boarding and Tarping Service, Perimeter Fencing, Emergency Tree Removal,

```html
<!DOCTYPE html>
<html lang="en">
<head>
<meta charset="utf-8">
<title>Halvorsen's Construction – Business Card</title>
<link rel="stylesheet" href="https://fonts.googleapis.com/css2?family=Lato:wght@400;700;900&display=swap">
<style>
  :root {
    --bg: #3a3a3c;
    --card-dark: #1c1c1e;
    --card-light: #ffffff;
    --brand-blue: #1594e6;
    --brand-blue-soft: #3aa8ef;
    --ink: #3b3b3d;
    --white: #ffffff;
  }
  * { box-sizing: border-box; margin: 0; padding: 0; }
  html, body { width: 1200px; height: 875px; overflow: hidden; }
  body {
    background: var(--bg);
    font-family: "Lato", sans-serif;
    position: relative;
  }
  .card {
    position: absolute;
    width: 560px;
    height: 320px;
    border-radius: 22px;
    overflow: hidden;
    box-shadow: 0 18px 40px rgba(0,0,0,.45);
  }

  /* Back of card */
  .card-back {
    left: 80px;
    top: 90px;
    background: var(--card-dark);
    display: flex;
    align-items: center;
    justify-content: center;
  }
  .wordmark {
    color: var(--brand-blue);
    font-weight: 400;
    text-align: center;
    line-height: 1;
    display: flex;
    align-items: center;
    gap: 14px;
  }
  .wordmark-square {
    width: 18px; height: 18px;
    background: var(--brand-blue);
    flex: none;
  }
  .wordmark-name { display: block; font-size: 52px; letter-spacing: 2px; }
  .wordmark-sub { display: block; font-size: 15px; letter-spacing: 9px; margin-top: 10px; }

  /* Front of card */
  .card-front {
    left: 560px;
    top: 465px;
    background: var(--card-light);
  }
  .front-panel {
    position: absolute;
    inset: 0;
    width: 100%;
    height: 100%;
  }
  .front-brand {
    position: absolute;
    left: 26px;
    top: 40px;
  }
  .front-brand .wordmark { gap: 10px; text-align: left; }
  .front-brand .wordmark-square { width: 12px; height: 12px; }
  .front-brand .wordmark-name { font-size: 30px; letter-spacing: 1px; }
  .front-brand .wordmark-sub { font-size: 9px; letter-spacing: 5px; margin-top: 6px; }

  .services {
    position: absolute;
    left: 28px;
    top: 122px;
    list-style: none;
    color: var(--ink);
    font-size: 13px;
    line-height: 20px;
  }
  .services li { display: flex; align-items: center; gap: 8px; }
  .tick { width: 12px; height: 12px; flex: none; }

  .owners {
    position: absolute;
    right: 28px;
    top: 34px;
    width: 220px;
    color: var(--white);
    text-align: right;
  }
  .owners-names {
    font-size: 34px;
    font-weight: 700;
    line-height: 1.05;
    letter-spacing: .5px;
    text-transform: uppercase;
  }
  .owners-role { font-size: 17px; margin-top: 4px; }
  .rule {
    display: block;
    width: 36px;
    height: 2px;
    background: var(--white);
    margin: 12px 0 12px auto;
  }
  .call-label { font-size: 15px; font-weight: 700; }
  .phone { font-size: 36px; font-weight: 900; letter-spacing: .5px; line-height: 1.1; }
  .licence { font-size: 16px; font-weight: 700; }
</style>
</head>
<body>

  <section class="card card-back" aria-label="Card back">
    <div class="wordmark">
      <span class="wordmark-square"></span>
      <span>
        <span class="wordmark-name">HALVORSEN'S</span>
        <span class="wordmark-sub">CONSTRUCTION L.L.C</span>
      </span>
    </div>
  </section>

  <section class="card card-front" aria-label="Card front">
    <svg class="front-panel" viewBox="0 0 560 320" preserveAspectRatio="none" aria-hidden="true">
      <polygon points="330,0 560,0 560,320 250,320 285,150 250,150" fill="var(--brand-blue)"/>
      <polygon points="380,0 560,0 560,200 420,320 330,320 360,150" fill="var(--brand-blue-soft)" opacity=".35"/>
    </svg>

    <div class="front-brand">
      <div class="wordmark">
        <span class="wordmark-square"></span>
        <span>
          <span class="wordmark-name">HALVORSEN'S</span>
          <span class="wordmark-sub">CONSTRUCTION L.L.C</span>
        </span>
      </div>
    </div>

    <ul class="services">
      <li><svg class="tick" viewBox="0 0 12 12"><circle cx="6" cy="6" r="6" fill="var(--brand-blue)"/><path d="M3.3 6.2l1.8 1.8 3.6-3.7" stroke="#fff" stroke-width="1.5" fill="none"/></svg>Disaster Recovery</li>
      <li><svg class="tick" viewBox="0 0 12 12"><circle cx="6" cy="6" r="6" fill="var(--brand-blue)"/><path d="M3.3 6.2l1.8 1.8 3.6-3.7" stroke="#fff" stroke-width="1.5" fill="none"/></svg>Storm Damage Restoration</li>
      <li><svg class="tick" viewBox="0 0 12 12"><circle cx="6" cy="6" r="6" fill="var(--brand-blue)"/><path d="M3.3 6.2l1.8 1.8 3.6-3.7" stroke="#fff" stroke-width="1.5" fill="none"/></svg>Proactive Disaster Plan Management</li>
      <li><svg class="tick" viewBox="0 0 12 12"><circle cx="6" cy="6" r="6" fill="var(--brand-blue)"/><path d="M3.3 6.2l1.8 1.8 3.6-3.7" stroke="#fff" stroke-width="1.5" fill="none"/></svg>Roof Repair / Restoration</li>
      <li><svg class="tick" viewBox="0 0 12 12"><circle cx="6" cy="6" r="6" fill="var(--brand-blue)"/><path d="M3.3 6.2l1.8 1.8 3.6-3.7" stroke="#fff" stroke-width="1.5" fill="none"/></svg>Structural Repair &amp; Reconstruction</li>
      <li><svg class="tick" viewBox="0 0 12 12"><circle cx="6" cy="6" r="6" fill="var(--brand-blue)"/><path d="M3.3 6.2l1.8 1.8 3.6-3.7" stroke="#fff" stroke-width="1.5" fill="none"/></svg>Emergency Boarding &amp; Tarping Service</li>
      <li><svg class="tick" viewBox="0 0 12 12"><circle cx="6" cy="6" r="6" fill="var(--brand-blue)"/><path d="M3.3 6.2l1.8 1.8 3.6-3.7" stroke="#fff" stroke-width="1.5" fill="none"/></svg>Perimeter Fencing</li>
      <li><svg class="tick" viewBox="0 0 12 12"><circle cx="6" cy="6" r="6" fill="var(--brand-blue)"/><path d="M3.3 6.2l1.8 1.8 3.6-3.7" stroke="#fff" stroke-width="1.5" fill="none"/></svg>Emergency Tree Removal</li>
    </ul>

    <div class="owners">
      <p class="owners-names">Milo<br>&amp; Trent</p>
      <p class="owners-role">Owner Operators</p>
      <span class="rule"></span>
      <p class="call-label">Call Us Today</p>
      <p class="phone">5083716254</p>
      <span class="rule"></span>
      <p class="licence">licensed &amp; insured</p>
    </div>
  </section>

</body>
</html>
```